American cannabis tech company business card design

Pavrel.com is seeking a modern, professional, and brand-aligned business card that represents our company and its core values: Mission, Story, Values, and Impact. As an innovative cannabis company, we want a business card that is not only visually appealing but also serves as a representation of who we are and what we stand for.

Project Scope: Design a double-sided business card that integrates our brand identity and core values. Incorporate our key brand elements, ensuring a sleek and contemporary aesthetic. Visually reflect our core values (Mission, Story, Values, Impact) in a way that is engaging yet professional.

Target Market(s)

Vendors, third parties,

Contact Information for Business Card

Contact details (name, title, email, phone, website, etc.)

Font styles to use
Other font styles liked:
• Caslon, Centra

Colors

Designer to choose colors to be used in the design.

Requirements
Must have
• Pavrel.com logo and branding A creative yet clean way to integrate our core values (Mission, Story, Values, Impact) Modern typography and a well-structured layout
Nice to have
• forest green, grey, white, black
Should not have
• references to marijuana, leafs, plants, or related product

```html
<!DOCTYPE html>
<html lang="en">
<head>
<meta charset="utf-8">
<title>Pavrel.com Business Card</title>
<link href="https://fonts.googleapis.com/css2?family=Playfair+Display:wght@700;900&family=Montserrat:wght@400;500&display=swap" rel="stylesheet">
<style>
  :root {
    --forest: #1e4522;
    --forest-deep: #173a1b;
    --paper: #ffffff;
    --ink: #1c1c1c;
    --rule: #8a8a8a;
    --backdrop: #e4e6e3;
  }
  * { box-sizing: border-box; margin: 0; padding: 0; }
  html, body { width: 1200px; height: 900px; overflow: hidden; }
  body {
    background: var(--backdrop);
    display: flex; flex-direction: column; align-items: center; justify-content: center;
    gap: 48px;
  }
  .card {
    position: relative;
    width: 680px; height: 388px;
    overflow: hidden;
    box-shadow: 0 10px 28px rgba(0,0,0,0.18);
  }
  .card--front { background: var(--paper); }
  .card--back {
    background: var(--forest);
    display: flex; align-items: center; justify-content: center;
  }
  .edge-bar { position: absolute; background: var(--forest); width: 34px; }
  .edge-bar--left { left: 0; top: 0; height: 210px; }
  .edge-bar--right { right: 0; bottom: 0; height: 210px; }

  .wordmark {
    font-family: "Playfair Display", serif;
    font-weight: 900;
    letter-spacing: -1px;
  }
  .card--front .wordmark {
    position: absolute; left: 78px; top: 150px;
    font-size: 62px; color: var(--forest); line-height: 1;
  }
  .card--back .wordmark { font-size: 128px; color: var(--paper); line-height: 1; }

  .divider {
    position: absolute; left: 355px; top: 110px;
    width: 1px; height: 190px; background: var(--rule);
  }
  .details { position: absolute; left: 378px; top: 112px; color: var(--ink); }
  .details__name {
    font-family: "Playfair Display", serif; font-weight: 700;
    font-size: 26px; color: var(--forest); line-height: 1.1;
  }
  .details__title {
    font-family: "Playfair Display", serif; font-weight: 700;
    font-size: 12px; color: var(--ink); margin-bottom: 14px;
  }
  .details__address, .contact-list {
    font-family: "Montserrat", sans-serif; font-size: 15px; line-height: 1.35;
  }
  .details__address { margin-bottom: 10px; }
  .contact-list { list-style: none; }
  .contact-list li { display: flex; align-items: center; gap: 8px; }
  .contact-list svg { width: 13px; height: 13px; flex: none; }
</style>
</head>
<body>
  <section class="card card--front">
    <div class="edge-bar edge-bar--left"></div>
    <div class="edge-bar edge-bar--right"></div>
    <div class="wordmark">PAVREL</div>
    <div class="divider"></div>
    <div class="details">
      <p class="details__name">Daniel Harper</p>
      <p class="details__title">Owner</p>
      <p class="details__address">418 Linden Ave, #112<br>Fairmont, OH 43010</p>
      <ul class="contact-list">
        <li>
          <svg viewBox="0 0 24 24" aria-hidden="true"><path fill="#1e4522" d="M6.6 10.8a15.1 15.1 0 0 0 6.6 6.6l2.2-2.2c.3-.3.7-.4 1-.2 1.1.4 2.3.6 3.6.6.6 0 1 .4 1 1V20c0 .6-.4 1-1 1A17 17 0 0 1 3 4c0-.6.4-1 1-1h3.5c.6 0 1 .4 1 1 0 1.3.2 2.5.6 3.6.1.3 0 .7-.2 1z"/></svg>
          555-014-2290
        </li>
        <li>
          <svg viewBox="0 0 24 24" aria-hidden="true"><rect x="2" y="5" width="20" height="14" rx="2" fill="#1e4522"/><path d="M3 6l9 7 9-7" stroke="#fff" stroke-width="1.8" fill="none"/></svg>
          info@pavrel.com
        </li>
        <li>
          <svg viewBox="0 0 24 24" aria-hidden="true"><circle cx="12" cy="12" r="10" fill="#1e4522"/><path d="M2 12h20M12 2c3 3 3 17 0 20M12 2c-3 3-3 17 0 20" stroke="#fff" stroke-width="1.5" fill="none"/></svg>
          www.pavrel.com
        </li>
      </ul>
    </div>
  </section>

  <section class="card card--back">
    <div class="wordmark">PAVREL</div>
  </section>
</body>
</html>
```